I need a business card for my original fine art pieces

I would like a business card design including a logo design for a new business in the art world. I am based in the Hunter Valley NSW Australia. I am a contemporary figurative, encaustic and wildlife artist. I would like to be able to upload my email and mobile number to this as well. This design should be one that I can incorporate into banners and flyers etc. Id like to incorporate one of my own images or partial image into the background or somewhere below. My initials are RJ and I would like these used as a logo type. I would like the use of some colour and it to be bright and catchy. The final design should communicate artwork custom made and commissions available.

Overview: Original Fine Artworks for sale, online, art galleries etc, Custom made to order and by commission.

Target market is world wide audience and corporate world

My figurative work is painted using acrylics in a lot of natural ochre colours that reflect the Australian Outback, on canvas, linen, paper or board: My encaustic work is created in a contemporary abstract style using a blow torch and a made with a medium of 100% pure bees wax, Damar resin, mixed media and coloured pigments, applied to Birch board. My wildlife are created using coloured pencil and mixed media on a variety of paper types or board.

```html
<!DOCTYPE html>
<html lang="en">
<head>
<meta charset="utf-8">
<title>Ruby Jarrah – Business Card</title>
<link rel="stylesheet" href="https://fonts.googleapis.com/css2?family=Cinzel:wght@400;500&family=Open+Sans:wght@400;700&display=swap">
<style>
  :root {
    --bg: #3a3a3c;
    --card-black: #0c0c0d;
    --card-white: #ecebed;
    --accent: #f0501c;
    --text-dark: #3b3b3b;
    --text-light: #e6e6e6;
  }
  * { margin: 0; padding: 0; box-sizing: border-box; }
  html, body { width: 1200px; height: 900px; overflow: hidden; }
  body {
    background: var(--bg);
    font-family: "Open Sans", Arial, sans-serif;
    position: relative;
  }
  .card {
    position: absolute;
    top: 305px;
    width: 500px;
    height: 290px;
    border-radius: 18px;
    overflow: hidden;
    box-shadow: 0 10px 24px rgba(0,0,0,.45);
  }
  .card--front { left: 75px; background: var(--card-white); }
  .card--back { left: 625px; background: var(--card-black); }

  .front-panel { position: absolute; inset: 0; }

  .monogram {
    position: absolute;
    left: 150px; top: 170px;
    transform: translate(-50%, -50%);
    font-family: "Cinzel", Georgia, serif;
    font-weight: 400;
    font-size: 86px;
    color: var(--card-white);
    letter-spacing: 2px;
    line-height: 1;
  }

  .contact {
    position: absolute;
    right: 26px; top: 34px;
    text-align: right;
    color: var(--text-dark);
    font-size: 13px;
    line-height: 1.4;
  }
  .contact__name {
    color: var(--accent);
    font-weight: 700;
    font-size: 17px;
    letter-spacing: .3px;
    line-height: 1.1;
  }
  .contact__role { font-size: 11.5px; letter-spacing: .3px; margin-bottom: 24px; }
  .contact__line { display: flex; justify-content: flex-end; align-items: center; gap: 8px; }
  .contact__line svg { width: 10px; height: 10px; flex: none; }
  .contact__address { margin-top: 26px; margin-right: 18px; }

  .brand {
    position: absolute;
    inset: 0;
    display: flex;
    flex-direction: column;
    align-items: center;
    justify-content: center;
    text-align: center;
  }
  .brand__initials {
    font-family: "Cinzel", Georgia, serif;
    font-size: 56px;
    color: var(--accent);
    line-height: 1;
    margin-bottom: 22px;
  }
  .brand__name {
    font-family: "Cinzel", Georgia, serif;
    font-size: 34px;
    color: var(--accent);
    letter-spacing: 1px;
    line-height: 1;
  }
  .brand__tagline {
    font-family: "Open Sans", Arial, sans-serif;
    font-size: 14.5px;
    color: var(--text-light);
    letter-spacing: 3.4px;
    margin-top: 4px;
  }
</style>
</head>
<body>

  <section class="card card--front" aria-label="Card front">
    <svg class="front-panel" viewBox="0 0 500 290" aria-hidden="true">
      <rect x="0" y="0" width="205" height="290" fill="var(--card-black)"/>
      <circle cx="150" cy="170" r="112" fill="var(--card-black)"/>
    </svg>
    <div class="monogram">RJ</div>

    <div class="contact">
      <div class="contact__name">ALEX CARTER</div>
      <div class="contact__role">GENERAL MANAGER</div>
      <div class="contact__line">(02) 4955-0182
        <svg viewBox="0 0 10 10"><path d="M2 1 L4 1 L4.6 3 L3.5 3.8 Q4.6 6 6.2 6.5 L7 5.4 L9 6 L9 8 Q8.5 9 7.5 9 Q1 8 1 2 Q1 1.2 2 1Z" fill="var(--accent)"/></svg>
      </div>
      <div class="contact__line">hello@rubyjarrah.art
        <svg viewBox="0 0 10 10"><rect x="0.5" y="2" width="9" height="6.5" rx="1" fill="var(--accent)"/><path d="M1 2.6 L5 5.6 L9 2.6" stroke="var(--card-white)" stroke-width="0.9" fill="none"/></svg>
      </div>
      <div class="contact__line">www.rubyjarrah.art
        <svg viewBox="0 0 10 10"><circle cx="5" cy="5" r="4.6" fill="var(--accent)"/><path d="M0.6 5 H9.4 M5 0.6 Q2.5 5 5 9.4 M5 0.6 Q7.5 5 5 9.4" stroke="var(--card-white)" stroke-width="0.7" fill="none"/></svg>
      </div>
      <div class="contact__address">42 Vineyard Lane,<br>Pokolbin, NSW 2320</div>
    </div>
  </section>

  <section class="card card--back" aria-label="Card back">
    <div class="brand">
      <div class="brand__initials">RJ</div>
      <div class="brand__name">RUBY JARRAH</div>
      <div class="brand__tagline">ORIGINAL FINE ARTWORKS</div>
    </div>
  </section>

</body>
</html>
```